Agriculture Business Card

I want to use my existing logo and use my tagline of "Don't Guess...Soil Test" on the card. Looking for a double sided card that will really get peoples attention.
Contact Info:
Marlow Field Crop Edge
Calvin Brusk
2917 K Lane
Larkin, NE 68593
402-555-0193
calvin.r.brusk@fieldmailbox.net

```html
<!DOCTYPE html>
<html lang="en">
<head>
<meta charset="utf-8">
<title>Marlow Field Crop Edge – Business Card</title>
<link href="https://fonts.googleapis.com/css2?family=Arimo:wght@400;700&display=swap" rel="stylesheet">
<style>
  :root {
    --backdrop: #e9e9e8;
    --card-white: #ffffff;
    --field-green: #3bb04a;
    --leaf-green: #2e9a3e;
    --soft-green: #8fcf88;
    --earth-brown: #8a4b2e;
    --ink-grey: #6b6b6b;
    --rule-grey: #b9b9b9;
  }
  * { margin: 0; padding: 0; box-sizing: border-box; }
  html, body {
    width: 1200px; height: 802px; overflow: hidden;
    background: var(--backdrop);
    font-family: "Arimo", Arial, sans-serif;
  }
  .sheet {
    width: 1200px; height: 802px;
    display: flex; align-items: center; justify-content: center; gap: 40px;
  }
  .card {
    position: relative;
    width: 540px; height: 309px;
    overflow: hidden;
    box-shadow: 0 6px 18px rgba(0,0,0,.18);
  }
  /* Front side */
  .card--front { background: var(--card-white); }
  .brand-mark {
    position: absolute; left: 44px; top: 58px;
    display: flex; align-items: center; gap: 12px;
  }
  .brand-mark__dot {
    width: 30px; height: 30px; border-radius: 50%;
    background: var(--field-green);
  }
  .brand-mark__name {
    font-weight: 700; font-size: 22px; line-height: 1.1;
    color: var(--earth-brown); width: 180px;
  }
  .holder-name {
    position: absolute; left: 44px; bottom: 48px;
    font-size: 26px; font-weight: 400; letter-spacing: .5px;
    color: var(--field-green); text-transform: uppercase;
  }
  .divider {
    position: absolute; left: 278px; top: 150px;
    width: 1px; height: 112px; background: var(--rule-grey);
  }
  .contact-list {
    position: absolute; left: 296px; top: 164px;
    list-style: none; font-size: 14.5px; color: var(--ink-grey);
  }
  .contact-list li { display: flex; align-items: center; gap: 8px; margin-bottom: 12px; }
  .contact-list li.no-icon { padding-left: 20px; }
  .contact-list svg { width: 12px; height: 12px; flex: none; }
  /* Back side */
  .card--back { background: var(--field-green); }
  .back-decoration {
    position: absolute; left: 40px; top: 40px;
    width: 250px; height: 260px; border-radius: 40px 40px 0 0;
    background: linear-gradient(160deg, var(--leaf-green) 0%, var(--soft-green) 100%);
    opacity: .55;
  }
  .back-title {
    position: absolute; right: 36px; top: 170px; width: 260px;
    text-align: right; color: var(--card-white);
    font-weight: 700; font-size: 27px; line-height: 1.05;
  }
  .back-tagline {
    position: absolute; right: 36px; top: 250px;
    color: var(--card-white); font-size: 15px; font-weight: 700;
  }
</style>
</head>
<body>
<main class="sheet">
  <section class="card card--front" aria-label="Card front">
    <div class="brand-mark">
      <span class="brand-mark__dot"></span>
      <span class="brand-mark__name">Marlow Field Crop Edge</span>
    </div>
    <p class="holder-name">Calvin Brusk</p>
    <span class="divider"></span>
    <ul class="contact-list">
      <li>
        <svg viewBox="0 0 12 12" aria-hidden="true"><path fill="#3bb04a" d="M2.5 1l2 2-1 1.3c.6 1.4 1.8 2.6 3.2 3.2L8 6.5l2 2-1.2 1.6C5.3 9.9 2.1 6.7 1 3.2z"/></svg>
        402-555-0193
      </li>
      <li>
        <svg viewBox="0 0 12 12" aria-hidden="true"><rect x="0.5" y="2.5" width="11" height="7" fill="#3bb04a"/><path d="M1 3l5 4 5-4" stroke="#fff" fill="none"/></svg>
        calvin.r.brusk@fieldmailbox.net
      </li>
      <li class="no-icon">2917 K Lane, Larkin, NE 68593</li>
    </ul>
  </section>

  <section class="card card--back" aria-label="Card back">
    <div class="back-decoration" role="img" aria-label="Faint large brand emblem decoration in green tones"></div>
    <p class="back-title">Marlow Field Crop Edge</p>
    <p class="back-tagline">Don't Guess...Soil Test</p>
  </section>
</main>
</body>
</html>
```